Financial Planning business needs a Web Design

Web design needed for financial planning business that encompasses investments, insurance and corporate planning. Would like a sleek, simple design that includes elements of nature/trees and lifestyle based imagery, with an overall feel of trustworthiness, security, growth and freedom. We like the layout of www.quellmarkroanefinancial.example, torvinfinancial.example and plomtavery.example, but with more color and images consistent with the nature/lifestyle theme.

Target Market(s)

New and existing clients

Industry/Entity Type

Financial

Number of Pages Required

5+ page

Requirements
Nice to have
• link to twitter feed
• 'latest features' link to articles
• links to action - buy insurance, get a quote, etc/

```html
<!DOCTYPE html>
<html lang="en">
<head>
<meta charset="utf-8">
<title>Alderwood Wealth Planning</title>
<link href="https://fonts.googleapis.com/css2?family=Open+Sans:wght@400;600;700&display=swap" rel="stylesheet">
<style>
:root{
  --forest-dark:#1d3a12;
  --forest-mid:#3f6b22;
  --brand-green:#1f6a2a;
  --brand-deep:#134d1c;
  --olive:#8aa834;
  --accent-red:#d2231b;
  --tweet-blue:#5d8fa8;
  --text:#333;
  --muted:#888;
  --nav-grey:#e2e2e2;
  --footer:#1e1e1e;
  --white:#fff;
}
*{margin:0;padding:0;box-sizing:border-box}
html,body{width:1000px;height:1200px;overflow:hidden}
body{font-family:"Open Sans",sans-serif;color:var(--text);position:relative;
  background:linear-gradient(180deg,#4c7a2c 0%,#2c4f17 35%,#1c3410 70%,#23401a 100%)}
.forest{position:absolute;inset:0}
.page{position:absolute;left:110px;top:20px;width:780px;height:1162px;background:var(--white)}
.abs{position:absolute}
.logo{left:10px;top:16px;display:flex;align-items:center;gap:8px}
.logo-mark{width:34px;height:34px;background:var(--brand-green);border-radius:50%}
.logo-name{font-size:17px;font-weight:600;color:var(--brand-green);line-height:1.05}
.logo-name small{display:block;font-size:7px;letter-spacing:2px;font-weight:600}
.header-phone{left:512px;top:37px;font-size:14px;font-weight:600;display:flex;align-items:center;gap:8px}
.btn{background:var(--brand-green);color:var(--white);font-weight:600;display:flex;align-items:center;justify-content:center;border-radius:2px}
.btn-buy{left:668px;top:32px;width:100px;height:26px;font-size:11px}
.nav{left:10px;top:88px;width:759px;height:32px;background:linear-gradient(#ececec,#d8d8d8);display:flex;font-size:10px;font-weight:600}
.nav a{color:var(--text);text-decoration:none;display:flex;align-items:center;justify-content:center;border-right:1px solid #c9c9c9}
.nav a.active{background:var(--brand-deep);color:var(--white)}
.hero{left:10px;top:132px;width:760px;height:346px;background:linear-gradient(120deg,#e9ece8 0%,#f4f4f0 45%,#dfe6d2 75%,#c9d6b4 100%)}
.hero-arrow{width:26px;height:26px;border-radius:50%;background:rgba(120,120,120,.7)}
.hero-caption{left:448px;top:237px;width:246px;height:89px;background:rgba(138,168,52,.92);color:var(--white);font-size:13px;font-weight:600;padding:20px 24px;line-height:1.4}
.welcome{left:40px;top:498px;width:700px;text-align:center}
.welcome h1{font-size:16px;font-weight:600;margin-bottom:9px}
.welcome p{font-size:8.6px;font-weight:600;color:#555;line-height:1.5}
.section-title{font-size:16px;font-weight:600}
.card{width:155px;height:144px;border:1px solid #eee}
.card-img{height:70px}
.card h3{font-size:11.5px;font-weight:400;line-height:1.5;padding:3px 6px 0;color:#444}
.card .meta{font-size:8px;color:var(--muted);padding:2px 6px}
.meta span{color:var(--accent-red)}
.stars{padding:0 6px;font-size:10px;letter-spacing:-1px;color:#f1b500}
.stars i{font-style:normal;color:#ccc}
.divider{left:524px;top:594px;width:1px;height:264px;background:#ddd}
.tweet{left:560px;width:175px;font-size:8.6px;line-height:1.55;color:var(--tweet-blue)}
.tweet b{color:var(--text);font-weight:400}
.tweet .when{color:var(--text)}
.tweet .when.new{color:var(--accent-red)}
.tweet-dot{left:560px;width:20px;height:20px;border-radius:50%}
.quote{left:559px;top:854px;width:204px;height:142px;background:#efefef;padding:10px 14px}
.quote h2{font-size:16px;font-weight:600;color:#333}
.quote p{font-size:8.6px;color:#777;line-height:1.4;margin-top:2px}
.quote-input{left:14px;top:61px;width:177px;height:29px;background:var(--white)}
.btn-quote{left:93px;top:99px;width:98px;height:28px;font-size:12px;background:var(--brand-deep)}
.footer{left:0;top:1019px;width:780px;height:143px;background:var(--footer);color:#ddd}
.footer-nav{left:12px;top:30px;display:flex;align-items:center;font-size:9px}
.footer-nav a{color:#ddd;text-decoration:none;padding:0 13px}
.footer-nav .sep{color:#999}
.footer-nav a.active{border:1px solid #ddd;border-radius:12px;padding:4px 10px}
.social{width:11px;height:11px;border-radius:50%;background:#ddd;top:30px}
.tip{left:692px;top:52px;width:50px;height:18px;border-radius:9px;background:var(--olive);color:var(--white);font-size:7px;font-weight:700;display:flex;align-items:center;justify-content:center}
.footer-line{left:12px;top:69px;width:756px;height:1px;background:#3a3a3a}
.contact-item{top:94px;display:flex;align-items:flex-start;gap:7px;font-size:8px;line-height:1.5}
.contact-item svg{flex:none}
.copyright{right:12px;top:97px;font-size:8.6px;color:#ccc}
</style>
</head>
<body>
<div class="forest" role="img" aria-label="Background photo of a dense green forest"></div>
<div class="page">
  <div class="abs logo"><div class="logo-mark"></div><div class="logo-name">Alderwood<small>WEALTH PLANNING</small></div></div>
  <div class="abs header-phone">+2 - 555 -01 - 2047
    <svg width="16" height="16" viewBox="0 0 16 16"><path d="M5 3.5l2 2-1.2 1.3c.6 1.3 1.6 2.3 2.9 2.9L10 8.5l2 2-1.5 1.5C7 12 4 9 3.5 5z" fill="none" stroke="#1f6a2a" stroke-width="1.3" stroke-linejoin="round"/></svg>
  </div>
  <div class="abs btn btn-buy">Buy Insurance</div>
  <nav class="abs nav">
    <a class="active" style="width:80px">Home</a>
    <a style="width:110px">What We Do</a>
    <a style="width:90px">Articles</a>
    <a style="width:78px">Team</a>
    <a style="width:104px">Newsletter</a>
    <a style="width:90px">Contact</a>
    <a style="width:76px;border-right:0">Login</a>
  </nav>
  <div class="abs hero" role="img" aria-label="Photo of hands using a calculator and pen over financial charts and tables">
    <div class="abs hero-arrow" style="left:2px;top:156px"></div>
    <div class="abs hero-arrow" style="left:696px;top:156px"></div>
    <div class="abs hero-caption">Lorem ipsum dolor sit amet, consectetur adipiscing elit. Sed efficitur</div>
  </div>
  <div class="abs welcome">
    <h1>Welcome To Our Site</h1>
    <p>Duis suscipit aliquet commodo. Aliquam ac finibus tortor. Vivamus rutrum finibus eros non rutrum. Curabitur nec urna vel turpis tincidunt fermentum eu ut purus. Vestibulum finibus augue a ante pretium accumsan. Suspendisse sit amet vestibulum augue. Nullam finibus molestie ligula mollis auctor. Etiam convallis sapien massa, et volutpat neque vulputate ac. Cras nec velit bibendum, feugiat ex sit amet, molestie justo. Donec viverra cursus sapien, ac congue turpis dictum sollicitudin. Lorem ipsum dolor sit amet, consectetur adipiscing elit. Sed efficitur efficitur orci, non tempor orci luctus ac.</p>
  </div>
  <h2 class="abs section-title" style="left:8px;top:590px">Latest Articles</h2>

  <article class="abs card" style="left:10px;top:634px"><div class="card-img" role="img" aria-label="Photo of business people reviewing a chart on a tablet" style="background:linear-gradient(135deg,#5b7ea8,#c9d8e8)"></div><h3>How to budget for living abroad</h3><p class="meta">Posted on <span>7 April, 2013</span> By <span>Lorem</span></p><div class="stars">★★<i>★★★</i></div></article>
  <article class="abs card" style="left:172px;top:634px"><div class="card-img" role="img" aria-label="Photo of a hand writing beside a calculator" style="background:linear-gradient(135deg,#c9a48a,#eceae6)"></div><h3>How to budget for living abroad</h3><p class="meta">Posted on <span>7 April, 2013</span> By <span>site dol</span></p><div class="stars">★★<i>★★★</i></div></article>
  <article class="abs card" style="left:332px;top:634px"><div class="card-img" role="img" aria-label="Photo of a keyboard and printed charts on a desk" style="background:linear-gradient(135deg,#3e5f86,#dde6ef)"></div><h3>How to budget for living abroad</h3><p class="meta">Posted on <span>7 April, 2013</span> By <span>Lorem</span></p><div class="stars">★★<i>★★★</i></div></article>
  <article class="abs card" style="left:10px;top:786px"><div class="card-img" role="img" aria-label="Photo of a hand touching a rising growth arrow" style="background:linear-gradient(135deg,#2f4560,#8aa0b8)"></div><h3>How to budget for living abroad</h3><p class="meta">Posted on <span>7 April, 2013</span> By <span>K-tanner</span></p><div class="stars">★★<i>★★★</i></div></article>
  <article class="abs card" style="left:172px;top:786px"><div class="card-img" role="img" aria-label="Photo of stacked coins on a financial chart" style="background:linear-gradient(135deg,#6e5030,#c8a46a)"></div><h3>How to budget for living abroad</h3><p class="meta">Posted on <span>7 April, 2013</span> By <span>K-tanner</span></p><div class="stars">★★<i>★★★</i></div></article>
  <article class="abs card" style="left:332px;top:786px"><div class="card-img" role="img" aria-label="Photo of a businessman with a briefcase looking out at the sea" style="background:linear-gradient(180deg,#d9dcde,#9a9688)"></div><h3>How to budget for living abroad</h3><p class="meta">Posted on <span>7 April, 2013</span> By <span>K-tanner</span></p><div class="stars">★★<i>★★★</i></div></article>

  <div class="abs divider"></div>
  <h2 class="abs section-title" style="left:560px;top:596px">Recent Tweets</h2>
  <div class="abs tweet-dot" style="top:640px;background:#2ba3c8;left:560px"></div>
  <p class="abs tweet" style="left:592px;top:638px;width:175px"><b>@sam_reyes</b> Curabitur rhoncus lorem a tortor luctus mollis non bibendum nisl. Pellentesque eros massa.<br><span class="when new">2 days ago</span></p>
  <div class="abs tweet-dot" style="top:710px;background:#c7cdd1"></div>
  <p class="abs tweet" style="left:592px;top:707px;width:175px">Lorem rhoncus lorem a tortor luctus mollis non bibendum nisl. Pellentesque eros <b>http://alder.example/ipsum</b><br><span class="when">3 days ago</span></p>
  <div class="abs tweet-dot" style="top:777px;background:#c7cdd1"></div>
  <p class="abs tweet" style="left:592px;top:774px;width:175px"><b>@lea_moran</b> Nunc sagittis purus quis molestie consequat. Donec a dui purus maecenas ac!<br><span class="when">5 days ago</span></p>

  <div class="abs quote">
    <h2>Get a Quote</h2>
    <p>Lorem ipsum dolor sit amet, consectetur adipiscing elit.</p>
    <div class="abs quote-input"></div>
    <div class="abs btn btn-quote">Get Now</div>
  </div>

  <footer class="abs footer">
    <div class="abs footer-nav">
      <a class="active">Home</a><a>What We Do</a><span class="sep">|</span><a>Articles</a><span class="sep">|</span><a>Team</a><span class="sep">|</span><a>Newsletter</a><span class="sep">|</span><a>Contact</a><span class="sep">|</span><a>Login</a>
    </div>
    <div class="abs social" style="left:689px"></div>
    <div class="abs social" style="left:711px"></div>
    <div class="abs social" style="left:734px"></div>
    <div class="abs social" style="left:758px"></div>
    <div class="abs tip">SHARE</div>
    <div class="abs footer-line"></div>
    <div class="abs contact-item" style="left:12px">
      <svg width="18" height="18" viewBox="0 0 18 18"><circle cx="9" cy="9" r="9" fill="#fff"/><path d="M9 4a3 3 0 0 0-3 3c0 2.3 3 6 3 6s3-3.7 3-6a3 3 0 0 0-3-3z" fill="#1e1e1e"/><circle cx="9" cy="7" r="1" fill="#fff"/></svg>
      <span>Brgy. Maliwan, Port Verano, Eastern Calora<br>4107, Philippines</span>
    </div>
    <div class="abs contact-item" style="left:274px;align-items:center">
      <svg width="18" height="18" viewBox="0 0 18 18"><circle cx="9" cy="9" r="9" fill="#fff"/><path d="M6 5l1.8 1.8-1 1c.6 1.3 1.4 2.1 2.6 2.6l1-1L12.2 11l-1.3 1.3C8 12 6 10 5.7 6.3z" fill="#1e1e1e"/></svg>
      <span>+ 63 900 555 0148</span>
    </div>
    <div class="abs contact-item" style="left:376px;align-items:center">
      <svg width="18" height="18" viewBox="0 0 18 18"><circle cx="9" cy="9" r="9" fill="#fff"/><rect x="5" y="6" width="8" height="6" fill="#1e1e1e"/><path d="M5 6l4 3.2L13 6" fill="none" stroke="#fff" stroke-width=".8"/></svg>
      <span style="font-weight:600">info@alderwood.example</span>
    </div>
    <div class="abs copyright">©Copyright 2015 alderwood. All Rights Reserved.</div>
  </footer>
</div>
</body>
</html>
```